Etikett für Likörflasche - Tinderbox
Zielgruppe
Wir sind eine kleine Tinderbox / Likörmanufaktur. Unser Obst für die Brände und Liköre stammt aus eigenem Anbau bzw. von umliegenden regionalen Bauern. Hier setzen wir auf sehr gute Qualität und verwenden keine Zusatzstoffe, Geschmacksverstärker, Farbstoffe etc. Im ersten Schritt werden wir nur 3-4 verschiedene Liköre anbieten.
Wir möchten unsere Liköre zukünftig auf Veranstaltungen / Events und Märkten verkaufen. Hierfür suchen wir ein pfiffiges und ansprechendes Etikettendesign.
Das Wort 'Tinderbox' soll die Leute auf den Events zu uns führen. Das wird auch mit großen Fahnen am Verkaufsstand beworben. Da wir auch ein paar amerikanische Foodtrucks haben soll auch das Etikett ein bisschen amerikanisch gehalten werden.
Zielgruppe: 28 bis 55 Jahre (Männer & Frauen)
Verkaufspreis pro 0,5 Liter Flasche ca. 24,50 Euro
Aufgabenstellung
Es soll ein Etikett auf die Flasche (nur vorne nicht auf die Rückseite).
Etikettengröße: ca. 7,0 x 8,5cm (für die 0,5l Flasche)
Angaben die sich auf dem Etikett ändern:
- Inhalt entweder 0,35l oder 0,5l Flasche
- Bezeichnung vom Inhalt und 'Kurzbeschreibung'
- Alkoholgehalt
Ich habe in PowerPoint schon mal ein Etikett zusammen gestellt, auf dem die Angaben alle mit enthalten sind. Hier fehlt mir allerdings der Pfiff und das Professionelle. Auch die Darstellung der Eigenschaften wie 'Echte Früchte', 'Handcrafted' etc. gefällt mir so auch nicht. Vielleicht wäre auch noch ein cooler Spruch darauf gut.
In die Anlage habe ich meine kreierte PowerPoint Folie gepackt (auf der 2. Folie findet ihr die geplante Flasche in die abgefüllt wird). Die zweite Datei ist ein Design was meinen Vorstellungen schon gut nahe kommt aus dem Internet (hier gefallen mir die Linien, kleine Gimmicks etc. da passiert einfach was auf dem Etikett). Von der Art her würde mir dieser Style gut gefallen. Es soll nur nicht zu überladen und kitschig werden.
Likörsorten die es geben wird: Wir werden uns erstmal auf 3-4 Sorten beschränken.

```html
<!DOCTYPE html>
<html lang="de">
<head>
<meta charset="utf-8">
<title>Harlan's Tinderbox – Etikett Rusty and Berry</title>
<link rel="stylesheet" href="https://fonts.googleapis.com/css2?family=Pathway+Gothic+One&family=Playfair+Display:wght@700&family=Kalam:wght@400&family=Permanent+Marker&display=swap">
<style>
  :root {
    --backdrop: #7d91a6;
    --label: #3a3a3c;
    --gold: #d9c08a;
    --cream: #efe3c4;
    --teal: #19a6b8;
    --teal-dark: #0f6f7c;
    --ink: #263238;
  }
  * { margin: 0; padding: 0; box-sizing: border-box; }
  html, body { width: 1200px; height: 2400px; overflow: hidden; }
  body { background: var(--backdrop); position: relative; }

  .label {
    position: absolute;
    left: 88px; top: 577px;
    width: 732px; height: 890px;
    transform: scale(1.4);
    transform-origin: 0 0;
  }
  .label-shape { position: absolute; inset: 0; width: 732px; height: 890px; }
  .label-text { position: absolute; white-space: nowrap; }
  .center { left: 0; width: 732px; text-align: center; }

  .brand-name {
    top: 168px;
    font-family: "Pathway Gothic One", sans-serif;
    font-size: 78px; letter-spacing: 2px;
    color: var(--gold);
  }
  .tagline-famous {
    left: 40px; top: 258px;
    font-family: "Permanent Marker", cursive;
    font-size: 19px; color: var(--teal);
  }
  .category {
    top: 286px;
    font-family: "Pathway Gothic One", sans-serif;
    font-size: 34px; color: var(--gold);
    font-variant: small-caps; letter-spacing: 1px;
  }
  .product-name {
    top: 338px;
    font-family: "Playfair Display", serif;
    font-weight: 700; font-size: 56px;
    color: var(--gold); letter-spacing: 1px;
  }
  .description {
    top: 430px;
    font-family: "Pathway Gothic One", sans-serif;
    font-size: 31px; line-height: 40px;
    color: var(--cream); letter-spacing: .5px;
  }
  .claim {
    font-family: "Kalam", cursive;
    font-size: 27px; line-height: 30px;
    color: var(--teal);
  }
  .claim-one-only { left: 28px; top: 452px; }
  .claim-real-taste { left: 622px; top: 446px; }
  .claim-handcrafted { left: 98px; top: 632px; }
  .claim-no-additives { left: 536px; top: 640px; }

  .spec-band {
    top: 561px;
    font-family: "Pathway Gothic One", sans-serif;
    font-size: 42px; color: var(--ink);
    word-spacing: 4px;
  }
  .spec-band .gap { display: inline-block; width: 34px; }

  .address {
    top: 694px;
    font-family: "Pathway Gothic One", sans-serif;
    font-size: 28px; line-height: 31px;
    color: var(--cream);
  }
  .website {
    top: 800px;
    font-family: "Pathway Gothic One", sans-serif;
    font-size: 27px; color: var(--gold);
  }
</style>
</head>
<body>
  <div class="label">
    <svg class="label-shape" viewBox="0 0 732 890" aria-hidden="true">
      <defs>
        <clipPath id="label-outline">
          <path d="M0,137 L97,137 A332,332 0 0 1 635,137 L732,137 L732,480 A366,410 0 0 1 0,480 Z"/>
        </clipPath>
        <radialGradient id="barrel-tone" cx="0.4" cy="0.5" r="0.6">
          <stop offset="0" stop-color="#1f7f8c" stop-opacity=".45"/>
          <stop offset="1" stop-color="#1f7f8c" stop-opacity="0"/>
        </radialGradient>
        <radialGradient id="wheat-tone" cx="0.5" cy="0.5" r="0.6">
          <stop offset="0" stop-color="#1f7f8c" stop-opacity=".4"/>
          <stop offset="1" stop-color="#1f7f8c" stop-opacity="0"/>
        </radialGradient>
      </defs>
      <path d="M0,137 L97,137 A332,332 0 0 1 635,137 L732,137 L732,480 A366,410 0 0 1 0,480 Z" fill="var(--label)"/>
      <g clip-path="url(#label-outline)">
        <rect x="0" y="410" width="250" height="320" fill="url(#barrel-tone)" role="img" aria-label="Skizze eines Holzfasses"/>
        <rect x="480" y="560" width="230" height="220" fill="url(#wheat-tone)" role="img" aria-label="Skizze von Getreideähren"/>
      </g>

      <!-- rules around product name -->
      <g stroke="var(--gold)" fill="none">
        <line x1="75" y1="330" x2="657" y2="330" stroke-width="2"/>
        <line x1="145" y1="336" x2="585" y2="336" stroke-width="1"/>
        <line x1="145" y1="406" x2="585" y2="406" stroke-width="1"/>
        <line x1="75" y1="412" x2="657" y2="412" stroke-width="2"/>
        <line x1="250" y1="662" x2="335" y2="662" stroke-width="2"/>
        <line x1="397" y1="662" x2="490" y2="662" stroke-width="2"/>
      </g>
      <polygon points="366,642 371,656 386,656 374,665 378,680 366,671 354,680 358,665 346,656 361,656" fill="var(--gold)"/>

      <!-- spec band -->
      <path d="M128,552 L605,552 Q618,585 605,618 L128,618 Q115,585 128,552 Z" fill="var(--teal)"/>
      <path d="M132,558 L601,558 Q612,585 601,612 L132,612 Q121,585 132,558 Z" fill="none" stroke="var(--teal-dark)" stroke-width="1.5"/>
      <circle cx="140" cy="585" r="2.5" fill="var(--ink)"/>
      <circle cx="593" cy="585" r="2.5" fill="var(--ink)"/>
    </svg>

    <div class="label-text center brand-name">HARLAN'S TINDERBOX</div>
    <div class="label-text tagline-famous">THE FAMOUS</div>
    <div class="label-text center category">Seasoned Fruits</div>
    <div class="label-text center product-name">RUSTY AND BERRY</div>
    <div class="label-text center description">WILDE BEEREN TREFFEN AUF VIELSCHICHTIGE<br>NOTEN VON WHISKEY UND KARAMELL</div>

    <div class="label-text claim claim-one-only">The One<br>&amp; Only</div>
    <div class="label-text claim claim-real-taste">Real<br>Taste</div>
    <div class="label-text claim claim-handcrafted">Complete<br>Handcrafted</div>
    <div class="label-text claim claim-no-additives">No Additives</div>

    <div class="label-text center spec-band">500 ML<span class="gap"></span>22 % VOL. 44 PROOF</div>

    <div class="label-text center address">HARLAN'S TINDERBOX<br>AM LINDENHANG 12<br>91234 FELDKIRCHEN</div>
    <div class="label-text center website">WWW.HARLANS-TINDERBOX.DE</div>
  </div>
</body>
</html>
```